Local Roofing/Construction company business needs new biz card design

We need a new business card design, current cards are from the start of this operation and generic at best. We are a local Construction Company (General Contractor) with a majority of our work originating from insurance claims-exterior finish work is the main focus (Roofs-Siding-Gutters etc). Heavily involved with homeowners and the low ball offers they receive from insurance company's after a insurable event takes place. I have attached some of our original logo file(s) below.

```html
<!DOCTYPE html>
<html lang="en">
<head>
<meta charset="utf-8">
<title>Stonefield Builders – Business Card</title>
<link href="https://fonts.googleapis.com/css2?family=Open+Sans:wght@400;600;700;800&display=swap" rel="stylesheet">
<style>
  :root {
    --backdrop: #232323;
    --brand-green: #52bc6e;
    --card-dark: #061c20;
    --card-dark-soft: #0a262b;
    --card-dark-deep: #041417;
    --ink-white: #ffffff;
    --ink-muted: #e6efe9;
  }
  * { box-sizing: border-box; margin: 0; padding: 0; }
  html, body {
    width: 1200px; height: 780px; overflow: hidden;
    background: var(--backdrop);
    font-family: "Open Sans", Arial, sans-serif;
  }
  .canvas { position: relative; width: 1200px; height: 780px; }

  .card {
    position: absolute; top: 90px;
    width: 343px; height: 600px;
    border-radius: 22px; overflow: hidden;
  }
  .card--front { left: 205px; background: var(--brand-green); }
  .card--back { left: 652px; background: var(--card-dark); }

  /* Front */
  .front-wordmark {
    position: absolute; left: 50%; top: 50%;
    transform: translate(-50%, -50%) rotate(90deg);
    display: flex; align-items: center; gap: 16px;
    white-space: nowrap;
  }
  .front-wordmark__square {
    width: 34px; height: 34px; background: var(--card-dark);
  }
  .front-wordmark__name {
    font-weight: 800; font-size: 38px; letter-spacing: 1px;
    color: var(--card-dark); text-transform: uppercase;
  }

  /* Back */
  .back-curves { position: absolute; inset: 0; }
  .back-brand {
    position: absolute; top: 50px; left: 0; right: 0;
    display: flex; justify-content: center; align-items: center; gap: 10px;
  }
  .back-brand__square { width: 18px; height: 18px; background: var(--brand-green); }
  .back-brand__name {
    font-weight: 800; font-size: 20px; letter-spacing: 1px;
    color: var(--brand-green); text-transform: uppercase;
  }
  .person { position: absolute; top: 190px; left: 0; right: 0; text-align: center; }
  .person__name { font-size: 27px; font-weight: 800; letter-spacing: .5px; }
  .person__first { color: var(--brand-green); }
  .person__last { color: var(--ink-white); }
  .person__role { font-size: 14px; font-weight: 600; color: var(--ink-white); margin-top: 2px; }

  .icon-row { display: flex; justify-content: center; gap: 8px; margin-top: 16px; }
  .icon-dot {
    width: 26px; height: 26px; border-radius: 50%;
    background: var(--brand-green);
    display: flex; align-items: center; justify-content: center;
  }
  .contact-list { list-style: none; margin-top: 12px; color: var(--ink-muted); font-size: 13.5px; line-height: 1.55; }

  .address { position: absolute; bottom: 62px; left: 0; right: 0; text-align: center; color: var(--ink-white); font-size: 14px; line-height: 1.5; }
  .address .icon-dot { margin: 0 auto 10px; }
</style>
</head>
<body>
<main class="canvas">

  <section class="card card--front" aria-label="Card front">
    <div class="front-wordmark">
      <span class="front-wordmark__square"></span>
      <span class="front-wordmark__name">Stonefield Builders</span>
    </div>
  </section>

  <section class="card card--back" aria-label="Card back">
    <svg class="back-curves" viewBox="0 0 343 600" preserveAspectRatio="none" aria-hidden="true">
      <path d="M0 600 L0 450 Q120 360 343 330 L343 600 Z" fill="var(--card-dark-deep)"/>
      <path d="M0 600 L0 520 Q170 400 343 380 L343 600 Z" fill="var(--card-dark-soft)" opacity=".6"/>
      <path d="M0 440 Q170 450 343 250 L343 300 Q190 480 0 465 Z" fill="var(--card-dark-deep)" opacity=".8"/>
    </svg>

    <div class="back-brand">
      <span class="back-brand__square"></span>
      <span class="back-brand__name">Stonefield Builders</span>
    </div>

    <div class="person">
      <p class="person__name"><span class="person__first">Dana</span> <span class="person__last">Whitlock</span></p>
      <p class="person__role">Co-Founder</p>

      <div class="icon-row">
        <span class="icon-dot" aria-label="Phone">
          <svg width="14" height="14" viewBox="0 0 24 24"><path d="M6.6 10.8a15 15 0 0 0 6.6 6.6l2.2-2.2c.3-.3.7-.4 1-.2 1.1.4 2.3.6 3.6.6.6 0 1 .4 1 1V20c0 .6-.4 1-1 1C10.6 21 3 13.4 3 4c0-.6.4-1 1-1h3.5c.6 0 1 .4 1 1 0 1.3.2 2.5.6 3.6.1.3 0 .7-.2 1z" fill="#fff"/></svg>
        </span>
        <span class="icon-dot" aria-label="Email">
          <svg width="14" height="14" viewBox="0 0 24 24"><rect x="3" y="6" width="18" height="12" rx="1.5" fill="none" stroke="#fff" stroke-width="2"/><path d="M3 7l9 6 9-6" fill="none" stroke="#fff" stroke-width="2"/></svg>
        </span>
        <span class="icon-dot" aria-label="Website">
          <svg width="14" height="14" viewBox="0 0 24 24"><circle cx="12" cy="12" r="9" fill="none" stroke="#fff" stroke-width="2"/><path d="M3 12h18M12 3c3 3 3 15 0 18M12 3c-3 3-3 15 0 18" fill="none" stroke="#fff" stroke-width="1.6"/></svg>
        </span>
      </div>

      <ul class="contact-list">
        <li>555-210-4837</li>
        <li>555-318-9062 (Emergency)</li>
        <li>www.stonefieldbuilders.com</li>
        <li>office@stonefieldbuilders.com</li>
      </ul>
    </div>

    <div class="address">
      <span class="icon-dot" aria-label="Location">
        <svg width="14" height="14" viewBox="0 0 24 24"><path d="M12 2a7 7 0 0 0-7 7c0 5 7 13 7 13s7-8 7-13a7 7 0 0 0-7-7z" fill="none" stroke="#fff" stroke-width="2"/><circle cx="12" cy="9" r="2.5" fill="#fff"/></svg>
      </span>
      <p>48 Harlow Ridge</p>
      <p>Rd, Millbrook, MO 63999</p>
    </div>
  </section>

</main>
</body>
</html>
```